Flyer for the Lumen 2025 Conference

I am looking to produce a flyer for our upcoming conference, Lumen 2025. This is an annual conference that we plan to publicize on social media. The ideal designer will create a flyer that is eye-catching and effectively communicates the key information. Please see attached our logo, speaker photo, and flyer content.

Target Market(s)

All demographics

Industry/Entity Type

Christian

Font styles to use
Sans Serif

Requirements
Should not have
• Cross, church

```html
<!DOCTYPE html>
<html lang="en">
<head>
<meta charset="utf-8">
<title>Lumen 2025 Conference Flyer</title>
<link rel="stylesheet" href="https://fonts.googleapis.com/css2?family=Bebas+Neue&family=Great+Vibes&family=Montserrat:wght@800;900&family=Poppins:wght@400;500;600;700;800&display=swap">
<style>
  :root {
    --stage: #1c2b3d;
    --navy-top: #0f4f94;
    --navy-bottom: #0a3769;
    --band-blue: #1660b8;
    --time-blue: #1d6fd1;
    --orange: #f28a25;
    --gold-light: #f6dca0;
    --gold-dark: #c98a3a;
    --white: #ffffff;
    --ink: #13294b;
    --pill: #dbe8f6;
  }
  * { margin: 0; padding: 0; box-sizing: border-box; }
  html, body { width: 1200px; height: 800px; overflow: hidden; }
  body {
    background: var(--stage);
    display: flex; align-items: center; justify-content: center;
    font-family: "Poppins", sans-serif;
  }
  .flyer {
    position: relative; width: 570px; height: 760px; overflow: hidden;
    background: linear-gradient(180deg, var(--navy-top) 0%, var(--navy-bottom) 100%);
    color: var(--white);
  }
  .abs { position: absolute; }
  .event-title {
    left: 124px; top: 22px;
    font-family: "Montserrat", sans-serif; font-weight: 900; font-size: 100px; line-height: 1;
    letter-spacing: -1px;
    background: linear-gradient(120deg, var(--gold-light) 0%, var(--gold-dark) 45%, var(--gold-light) 70%, var(--gold-dark) 100%);
    -webkit-background-clip: text; background-clip: text; color: transparent;
  }
  .event-year {
    left: 340px; top: 122px;
    font-family: "Montserrat", sans-serif; font-weight: 900; font-size: 78px; line-height: 1;
    color: var(--white);
  }
  .conference-band {
    left: 30px; top: 135px; width: 300px; height: 31px;
    background: linear-gradient(90deg, var(--band-blue) 0%, var(--band-blue) 70%, rgba(22,96,184,0) 100%);
    font-weight: 700; font-size: 15px; letter-spacing: 2px; line-height: 31px; padding-left: 18px;
  }
  .topic-label {
    left: 124px; top: 174px; font-family: "Great Vibes", cursive; font-size: 34px; color: var(--orange);
    line-height: 1; transform: rotate(-6deg);
  }
  .topic-title { left: 204px; top: 176px; font-weight: 700; font-size: 19px; line-height: 24px; }
  .speaker-photo {
    left: 0; top: 170px; width: 300px; height: 460px;
    background: radial-gradient(ellipse at 35% 30%, #f5a341 0%, #d36a1e 30%, rgba(19,86,170,0.9) 60%, rgba(23,98,196,1) 100%);
    border-top-right-radius: 140px;
  }
  .date-block { left: 296px; width: 262px; height: 68px; }
  .date-frame {
    position: absolute; left: 0; top: 0; width: 180px; height: 68px;
    border-left: 1px dashed var(--orange); border-top: 1px dashed var(--orange);
    border-top-left-radius: 6px;
  }
  .date-day {
    position: absolute; right: 4px; top: -14px; font-family: "Great Vibes", cursive;
    font-size: 28px; line-height: 1; color: var(--white);
  }
  .date-num {
    position: absolute; left: 24px; top: 10px; font-family: "Bebas Neue", sans-serif;
    font-size: 62px; line-height: 1;
  }
  .date-ord {
    position: absolute; left: 72px; top: 10px; font-family: "Bebas Neue", sans-serif;
    font-size: 32px; line-height: 1;
  }
  .date-month {
    position: absolute; left: 101px; top: 10px; font-weight: 800; font-size: 26px; line-height: 1;
    color: var(--orange);
  }
  .date-time {
    position: absolute; left: 72px; top: 44px; width: 168px; height: 20px;
    background: var(--time-blue); border-radius: 2px;
    font-weight: 700; font-size: 17px; line-height: 20px; text-align: center;
  }
  .venue { left: 304px; top: 548px; display: flex; gap: 6px; }
  .venue-name { color: var(--orange); font-weight: 700; font-size: 16px; line-height: 20px; }
  .venue-address { font-size: 15px; line-height: 20px; }
  .footer { left: 0; top: 642px; width: 570px; height: 118px; background: var(--white); }
  .speaker-band {
    left: 0; top: 626px; width: 298px; height: 33px; background: var(--orange);
    border-radius: 0 3px 3px 0;
    font-family: "Bebas Neue", sans-serif; font-size: 25px; line-height: 35px; padding-left: 32px;
    color: var(--white);
  }
  .app-promo { left: 33px; top: 670px; color: var(--ink); }
  .app-kicker { color: var(--orange); font-weight: 600; font-size: 10px; line-height: 13px; }
  .app-title { font-weight: 600; font-size: 14px; line-height: 17px; }
  .app-note { color: var(--orange); font-weight: 600; font-size: 9.5px; line-height: 12px; }
  .store-badges { display: flex; gap: 4px; margin-top: 7px; }
  .store-badge { width: 61px; height: 21px; border: 1px solid #333; border-radius: 3px; background: var(--white); }
  .contacts { left: 211px; top: 675px; display: flex; flex-direction: column; gap: 6px; }
  .contact-pill {
    width: 153px; height: 17px; background: var(--pill); border-radius: 9px;
    display: flex; align-items: center; gap: 8px; padding-left: 4px;
    color: var(--ink); font-size: 11.5px; font-weight: 500;
  }
  .contact-pill svg { width: 12px; height: 12px; flex: none; }
  .org-name {
    left: 404px; top: 688px; display: flex; align-items: center; gap: 6px;
    font-weight: 600; font-size: 30px; color: var(--ink); line-height: 1;
  }
  .org-dot { width: 12px; height: 12px; border-radius: 50%; background: var(--orange); }
</style>
</head>
<body>
  <main class="flyer">
    <div class="abs speaker-photo" role="img" aria-label="Portrait photo of the speaker in a blue blazer against a warm orange glow"></div>

    <h1 class="abs event-title">LUMEN</h1>
    <div class="abs event-year">2025</div>
    <div class="abs conference-band">A PROPHETIC CONFERENCE</div>
    <div class="abs topic-label">Topic</div>
    <div class="abs topic-title">The Voice<br>Of The Lord</div>

    <section class="abs date-block" style="top:244px">
      <div class="date-frame"></div>
      <span class="date-day">Friday</span>
      <span class="date-num">26</span><span class="date-ord">TH</span>
      <span class="date-month">December</span>
      <span class="date-time">6:30PM – 9:00PM</span>
    </section>
    <section class="abs date-block" style="top:340px">
      <div class="date-frame"></div>
      <span class="date-day">Saturday</span>
      <span class="date-num">27</span><span class="date-ord">TH</span>
      <span class="date-month">December</span>
      <span class="date-time">5:30PM – 8:00PM</span>
    </section>
    <section class="abs date-block" style="top:437px">
      <div class="date-frame"></div>
      <span class="date-day">Sunday</span>
      <span class="date-num">28</span><span class="date-ord">TH</span>
      <span class="date-month">December</span>
      <span class="date-time">4:30PM – 7:00PM</span>
    </section>

    <address class="abs venue" style="font-style:normal">
      <svg width="18" height="18" viewBox="0 0 24 24" aria-hidden="true"><circle cx="12" cy="12" r="11" fill="var(--orange)"/><path d="M12 5a4.5 4.5 0 0 0-4.5 4.5c0 3.4 4.5 8.5 4.5 8.5s4.5-5.1 4.5-8.5A4.5 4.5 0 0 0 12 5z" fill="#fff"/><circle cx="12" cy="9.5" r="1.7" fill="var(--orange)"/></svg>
      <div>
        <div class="venue-name">The Harborview Performing<br>Arts Center</div>
        <div class="venue-address">88 Linden Mill Road<br>Fairhaven, Maine 04000</div>
      </div>
    </address>

    <div class="abs footer"></div>
    <div class="abs speaker-band">SPEAKER: PROPHET SAMUEL ARDELL</div>

    <div class="abs app-promo">
      <div class="app-kicker">Download</div>
      <div class="app-title">The KAELO App</div>
      <div class="app-note">to stay updated on the event</div>
      <div class="store-badges"><span class="store-badge"></span><span class="store-badge"></span></div>
    </div>

    <div class="abs contacts">
      <div class="contact-pill"><svg viewBox="0 0 24 24" aria-hidden="true"><circle cx="12" cy="12" r="12" fill="var(--ink)"/><path d="M8.5 6.5l2 2.3-1.2 1.5c.8 1.7 2.2 3.1 3.9 3.9l1.5-1.2 2.3 2-1.2 2c-4.6-.4-8.9-4.7-9.3-9.3z" fill="#fff"/></svg>555 014 2290</div>
      <div class="contact-pill"><svg viewBox="0 0 24 24" aria-hidden="true"><circle cx="12" cy="12" r="12" fill="var(--ink)"/><rect x="6" y="8" width="12" height="8" rx="1" fill="none" stroke="#fff" stroke-width="1.5"/><path d="M6.5 8.5l5.5 4 5.5-4" fill="none" stroke="#fff" stroke-width="1.5"/></svg>hello@kaelo.org</div>
      <div class="contact-pill"><svg viewBox="0 0 24 24" aria-hidden="true"><circle cx="12" cy="12" r="12" fill="var(--ink)"/><circle cx="12" cy="12" r="6" fill="none" stroke="#fff" stroke-width="1.3"/><path d="M6 12h12M12 6c-2.5 3.5-2.5 8.5 0 12M12 6c2.5 3.5 2.5 8.5 0 12" fill="none" stroke="#fff" stroke-width="1.3"/></svg><span style="font-weight:600;letter-spacing:1.5px">www.kaelo.org</span></div>
    </div>

    <div class="abs org-name"><span class="org-dot"></span>KAELO</div>
  </main>
</body>
</html>
```